Trovanta Overview and Demo Presentation

Objective:
Create a bold, visually engaging PowerPoint deck to present Trovanta’s sales process and system demo to local movers, emphasizing ease of use, increased profitability, and operational efficiency.
Key Elements:
• Design: High-impact graphics with Trovanta branding, minimal text, and clean layouts.
• Content: Step-by-step sales process, key selling points, system demo walkthrough, and a compelling call-to-action.
• Live Demo: Showcase Trovanta’s platform, focusing on instant guaranteed pricing, streamlined booking, and support features.
Deliverables:
A dynamic presentation designed to educate and convert local movers into Trovanta partners, ensuring seamless flow and strong audience engagement.

Target Market(s)

Local Movers

Industry/Entity Type

Household Goods Moving

Font styles to use
Sans Serif

Colors
0054AA
0677BA
7BADD7
CADEEF
E8F1F8
FFC000
F8CF3A
FAE287
FDF2CF
FEFAEE

Requirements
Must have
• Project Brief: Trovanta Sales Process Presentation Objective: Create a bold, visually engaging PowerPoint deck to present Trovanta’s sales process and system demo to local movers, emphasizing ease of use, increased profitability, and operational efficiency. Key Elements: • Design: High-impact graphics with Trovanta branding, minimal text, and clean layouts. • Content: Step-by-step sales process, key selling points, system demo walkthrough, and a compelling call-to-action. • Live Demo: Showcase Trovanta’s platform, focusing on instant guaranteed pricing, streamlined booking, and support features. Deliverables: A dynamic presentation designed to educate and convert local movers into Trovanta partners, ensuring seamless flow and strong audience engagement.

```html
<!DOCTYPE html>
<html lang="en">
<head>
<meta charset="utf-8">
<title>Trovanta Partner Overview Deck</title>
<link href="https://fonts.googleapis.com/css2?family=Montserrat:wght@400;500;600;700;800&display=swap" rel="stylesheet">
<style>
:root{
  --blue:#2353cf;
  --blue-deep:#1c45b5;
  --orange:#f8a623;
  --orange-soft:#fdf2cf;
  --yellow:#f8cf3a;
  --ink:#111;
  --grey-text:#666;
  --canvas:#c9c9c9;
  --white:#fff;
}
*{margin:0;padding:0;box-sizing:border-box}
html,body{width:1200px;height:349px;overflow:hidden;background:var(--canvas);font-family:"Montserrat",sans-serif;color:var(--ink)}
.deck{position:relative;width:1200px;height:349px}
.slide{position:absolute;width:287px;height:161px;background:var(--white);overflow:hidden;box-shadow:0 1px 2px rgba(0,0,0,.15)}
.abs{position:absolute}
.footer-band{position:absolute;left:0;right:0;bottom:0;height:12px;background:var(--orange)}
.footer-brand{position:absolute;left:0;bottom:0;width:56px;height:13px;background:var(--white);font-weight:700;color:var(--blue);font-size:8px;line-height:13px;padding-left:5px;letter-spacing:.3px}
.page-no{position:absolute;right:5px;bottom:3px;font-size:2.8px;color:#333}
.slide-title{position:absolute;left:0;right:0;text-align:center;font-weight:800;font-size:7.6px;letter-spacing:.1px}
.slide-title em{font-style:normal;color:var(--blue)}
.title-rule{position:absolute;left:50%;width:20px;margin-left:-10px;height:1.3px;background:var(--orange)}
.photo{position:absolute}
.tiny{font-size:3.1px;line-height:1.55;color:var(--grey-text)}
.card{position:absolute;background:var(--white);border:.6px solid #f1d9a8;box-shadow:0 .5px 2px rgba(0,0,0,.1)}
.check-box{position:absolute;background:var(--white);border:.7px solid var(--blue);border-radius:1.5px;padding:6px 5px}
.check-box h4{font-size:3.6px;font-weight:700;line-height:1.5;width:70%}
.check-box .num{position:absolute;right:5px;top:5px;font-size:9px;font-weight:600;color:var(--orange)}
.check-box p{margin-top:5px}
.vision-card{position:absolute;top:56px;width:65px;height:91px;background:var(--white);box-shadow:0 .5px 2px rgba(0,0,0,.15);text-align:center;padding:4px 3px}
.vision-card .dot{width:18px;height:18px;border-radius:50%;background:var(--yellow);margin:0 auto 4px}
.vision-card h5{font-size:3.6px;color:var(--blue);font-weight:600}
.vision-card h6{font-size:3px;font-weight:700;line-height:1.5;margin:1px 0 3px}
.vision-card p{font-size:2.9px;line-height:1.6;color:var(--grey-text)}
.step-label{position:absolute;top:93px;width:54px;text-align:center;font-size:3.9px;line-height:1.6;font-weight:500}
.step-label.orange{color:var(--orange)}
.step-label.dark{color:#222}
.metric{position:absolute;background:var(--white);box-shadow:0 .5px 2.5px rgba(0,0,0,.18);text-align:center}
.metric .cap{position:absolute;left:0;right:0;top:0;height:20px;background:var(--orange);border-radius:0 0 50% 50%/0 0 100% 100%;font-weight:800;font-size:8.5px;line-height:20px;color:#1a1a1a}
.metric p{position:absolute;left:4px;right:4px;font-size:3.6px;line-height:1.75;color:#444}
.trac{position:absolute;text-align:center;padding:10px 5px 0;box-shadow:0 .5px 2.5px rgba(0,0,0,.15);border:.6px solid #f3e0b8}
.trac h5{font-size:4.2px;font-weight:700;line-height:1.6;margin-bottom:5px}
.trac p{font-size:3.5px;line-height:1.6}
.trac.blue{background:var(--blue);color:var(--white);border-color:var(--blue)}
.trac.blue h5,.trac.white h5{color:inherit}
.trac.white{background:var(--white);color:#444}
.trac.white h5{color:var(--blue)}
.trac.orange{background:var(--orange);color:#3a2a00}
.trac.orange h5{color:#1a1a1a}
.contact-row{position:absolute;left:145px;display:flex;align-items:center;gap:5px;color:var(--white);font-size:4.9px;font-weight:600;line-height:1.7}
.contact-row .ico{width:12px;height:12px;border:.7px solid var(--white);border-radius:2px;display:flex;align-items:center;justify-content:center;flex:none}
</style>
</head>
<body>
<div class="deck">

  <!-- Slide 1: cover -->
  <section class="slide" style="left:12px;top:8px;background:linear-gradient(90deg,#fbfbfb 0%,#f1f0ee 60%,#e6e2dc 100%)">
    <div class="abs" style="left:22px;top:35px;font-weight:700;font-size:20px;color:var(--blue);letter-spacing:1px">Trovanta</div>
    <div class="abs" style="left:8px;top:70px;width:155px;text-align:center;font-weight:700;font-size:10px;line-height:1.25;color:var(--blue)">MOVING FOR THE NEXT GENERATION</div>
    <div class="abs" style="left:21px;top:101px;width:107px;height:.8px;background:var(--orange)"></div>
    <div class="abs" style="left:8px;top:110px;width:155px;text-align:center;font-size:5.4px;color:#333">Partner Overview Presentation</div>
    <div class="photo" role="img" aria-label="Movers carrying boxes seen through angled orange panels" style="left:170px;top:20px;width:113px;height:112px;background:linear-gradient(100deg,#f3a93a 0%,#e8c99a 30%,#f4ead9 45%,#f2a636 60%,#c7b69a 80%,#7c8f50 100%);clip-path:polygon(0 12%,100% 0,100% 100%,0 88%)"></div>
    <div class="footer-band" style="height:11px"></div>
    <div class="abs" style="left:4px;bottom:3px;font-size:2.8px;color:#222">February 1, 2024</div>
    <div class="page-no">www.trovanta.com</div>
  </section>

  <!-- Slide 2: about -->
  <section class="slide" style="left:307px;top:8px">
    <div class="photo" role="img" aria-label="Two movers in blue uniforms carrying cardboard boxes from a van" style="left:4px;top:0;width:115px;height:126px;background:linear-gradient(160deg,#6f6a63 0%,#b79b74 40%,#2f56b0 75%,#3b3d44 100%)"></div>
    <div class="abs" style="left:133px;top:19px;font-weight:700;font-size:7.6px"><span style="color:var(--blue)">ABOUT</span> US</div>
    <div class="abs" style="left:133px;top:30px;width:22px;height:1.3px;background:var(--orange)"></div>
    <p class="abs tiny" style="left:141px;top:42px;width:124px"><b style="color:var(--blue);font-weight:600">Trovanta</b> is the next logical evolution in professional moving. Professional moving clients have battled soaring prices, acute capacity problems and deteriorating service levels.</p>
    <p class="abs tiny" style="left:141px;top:68px;width:124px"><b style="color:var(--blue);font-weight:600">Trovanta</b> was founded by lifelong moving professionals who have developed the answer to better moving services. Poised as THE industry disruptor, we deliver faster, offer guaranteed prices and even offer no credit check financing options. We are a technology first organization using proprietary software to deliver moving's best service experience</p>
    <div class="footer-band"></div><div class="footer-brand">Trovanta</div><div class="page-no">Page 02</div>
  </section>

  <!-- Slide 3: checks and balances -->
  <section class="slide" style="left:604px;top:8px">
    <h2 class="slide-title" style="top:17px">TROVANTA BUILT-IN <em>CHECKS AND BALANCES</em></h2>
    <div class="check-box" style="left:13px;top:42px;width:71px;height:49px"><h4>Independent Survey Company</h4><span class="num">1</span><p class="tiny">Trovanta automatically audits: Compliance, Insurance, Regulatory, Bonding, Background checks, and Quality.</p></div>
    <div class="check-box" style="left:13px;top:96px;width:71px;height:49px"><h4>Concierge Service</h4><span class="num">3</span><p class="tiny">Proven, proactive process operated by our award-winning team of experienced customer service professionals.</p></div>
    <div class="check-box" style="left:201px;top:42px;width:71px;height:49px"><h4>Multiple Network Service Providers</h4><span class="num">2</span><p class="tiny">With several professional teams engaged there are a series of checks and cross checks.</p></div>
    <div class="check-box" style="left:201px;top:96px;width:71px;height:49px"><h4>Immediate Capacity Secured</h4><span class="num">4</span><p class="tiny">Virtually limitless capacity even during peak moving days.</p></div>
    <svg class="abs" style="left:92px;top:40px" width="104" height="104" viewBox="0 0 104 104">
      <circle cx="52" cy="52" r="48" fill="none" stroke="#555" stroke-width=".5" stroke-dasharray="1.5 1.2"/>
      <circle cx="52" cy="52" r="41" fill="#fff" stroke="var(--yellow)" stroke-width="3"/>
      <circle cx="52" cy="52" r="38" fill="#fff" stroke="var(--blue)" stroke-width=".5"/>
      <circle cx="18" cy="18" r="10" fill="var(--blue)"/><circle cx="86" cy="18" r="10" fill="var(--blue)"/>
      <circle cx="18" cy="86" r="10" fill="var(--blue)"/><circle cx="86" cy="86" r="10" fill="var(--blue)"/>
    </svg>
    <div class="photo" role="img" aria-label="Balance scale holding two moving trucks" style="left:122px;top:58px;width:44px;height:24px;background:linear-gradient(180deg,#f7c948,#fbe9b0);border-radius:3px"></div>
    <div class="abs" style="left:118px;top:86px;width:52px;text-align:center;font-size:3.2px;line-height:1.7;color:var(--blue);font-weight:600">Independent groups working together to mitigate risk and error</div>
    <div class="footer-band"></div><div class="footer-brand">Trovanta</div><div class="page-no">Page 03</div>
  </section>

  <!-- Slide 4: vision -->
  <section class="slide" style="left:900px;top:8px">
    <div class="abs" style="left:12px;top:19px;font-weight:800;font-size:7.6px">OUR <span style="color:var(--blue)">VISION</span></div>
    <div class="abs" style="left:12px;top:31px;width:22px;height:1.3px;background:var(--orange)"></div>
    <div class="photo" role="img" aria-label="Young man packing moving boxes at a desk" style="left:172px;top:0;width:115px;height:56px;background:linear-gradient(120deg,#d9d2c6,#b88d5c 60%,#e7e1d8)"></div>
    <div class="photo" role="img" aria-label="Two smiling movers in blue uniforms giving thumbs up" style="left:208px;top:60px;width:79px;height:84px;background:linear-gradient(160deg,#d9dde3,#2b55b8 55%,#1e3f8f)"></div>
    <div class="vision-card" style="left:6px"><div class="dot"></div><h5>Our Vision</h5><h6>Revolutionize the moving industry by providing great value to everyone involved</h6><p>Trovanta Customers - Consumers, Movers, Corporate Clients, and Relocation Management Companies all receive better value with Trovanta than anywhere else.</p></div>
    <div class="vision-card" style="left:75px"><div class="dot"></div><h5>Our Mission</h5><h6>Disrupt a $86B sleepy giant of an inefficient industry</h6><p>Trovanta's deep understanding of the professional moving industry, supported by extensive market research has set Trovanta up for ultimate success in disrupting this industry by creating cost-saving efficiencies throughout.</p></div>
    <div class="vision-card" style="left:142px"><div class="dot"></div><h5>Our Goal</h5><h6>Becoming the moving platform of choice</h6><p>As Trovanta's market share grows, the customer acquisition cost and operational cost plummets. This creates even more market penetration, more efficiencies, and exponential growth.</p></div>
    <div class="footer-band"></div><div class="footer-brand">Trovanta</div><div class="page-no">Page 04</div>
  </section>

  <!-- Slide 5: accomplishments -->
  <section class="slide" style="left:12px;top:177px">
    <h2 class="slide-title" style="top:13px">WHAT TROVANTA <em>HAS ACCOMPLISHED</em></h2>
    <div class="title-rule" style="top:27px"></div>
    <svg class="abs" style="left:10px;top:55px" width="268" height="36" viewBox="0 0 268 36">
      <g font-family="Montserrat,sans-serif" font-size="3.6" text-anchor="middle">
        <path d="M0 12h46l5 6-5 6H0l5-6z" fill="var(--orange)"/><circle cx="26" cy="18" r="11" fill="var(--orange)" stroke="#fff" stroke-width="1"/><text x="21" y="4" fill="var(--orange)">01</text>
        <path d="M53 12h46l5 6-5 6H53l5-6z" fill="var(--blue-deep)"/><circle cx="79" cy="18" r="11" fill="var(--blue-deep)" stroke="#fff" stroke-width="1"/><text x="74" y="4" fill="#222">02</text>
        <path d="M106 12h46l5 6-5 6h-46l5-6z" fill="var(--orange)"/><circle cx="132" cy="18" r="11" fill="var(--orange)" stroke="#fff" stroke-width="1"/><text x="127" y="4" fill="var(--orange)">03</text>
        <path d="M159 12h46l5 6-5 6h-46l5-6z" fill="var(--blue-deep)"/><circle cx="185" cy="18" r="11" fill="var(--blue-deep)" stroke="#fff" stroke-width="1"/><text x="180" y="4" fill="#222">04</text>
        <path d="M212 12h46l5 6-5 6h-46l5-6z" fill="var(--orange)"/><circle cx="238" cy="18" r="11" fill="var(--orange)" stroke="#fff" stroke-width="1"/><text x="233" y="4" fill="var(--orange)">05</text>
      </g>
      <g fill="none" stroke="#fff" stroke-width=".7">
        <circle cx="26" cy="18" r="5"/><path d="M75 22v-4m3 4v-7m3 7v-5"/><circle cx="132" cy="18" r="5"/><rect x="181" y="14" width="8" height="8"/><path d="M233 22l4-4 2 2 4-5"/>
      </g>
    </svg>
    <div class="step-label orange" style="left:21px">Eliminate Capacity Constraints</div>
    <div class="step-label dark" style="left:75px">Reduce Costs</div>
    <div class="step-label orange" style="left:128px">Improve Service Levels</div>
    <div class="step-label dark" style="left:181px">Simplify the Moving Process</div>
    <div class="step-label orange" style="left:234px">Break the Typical Moving Mold</div>
    <div class="footer-band"></div><div class="footer-brand">Trovanta</div><div class="page-no">Page 05</div>
  </section>

  <!-- Slide 6: B2B expansion -->
  <section class="slide" style="left:307px;top:177px">
    <h2 class="slide-title" style="top:13px"><em>CORPORATE RELOCATION</em> EXPANDING INTO B2B</h2>
    <div class="title-rule" style="top:27px"></div>
    <div class="abs" style="left:0;right:0;top:34px;text-align:center;font-size:3.6px;font-weight:700;color:var(--blue)">CORPORATE RELOCATION PARTNERSHIPS</div>
    <p class="abs" style="left:5px;top:45px;width:122px;font-size:3.6px;line-height:1.7;color:#333">After proving the B2I model, Trovanta will concurrently expand into B2B, focusing on corporate relocation services for Fortune 1000 companies. This segment provides high-margin opportunities and long-term contracts.</p>
    <div class="photo" role="img" aria-label="Trading dashboard screen with tables and a blue area chart" style="left:4px;top:75px;width:133px;height:68px;border:.8px solid #99a;background:linear-gradient(180deg,#f4f6f9 0%,#e3e8ef 60%,#2f6fcf 80%,#1f3f78 100%)"></div>
    <div class="metric" style="left:178px;top:44px;width:65px;height:48px"><div class="cap">XXX</div><p style="top:25px">Annual Moves from B2B moves/year from secured corporate contracts</p></div>
    <div class="metric" style="left:145px;top:96px;width:64px;height:48px"><div class="cap">$XXX</div><p style="top:27px">Estimated Gross Profit</p></div>
    <div class="metric" style="left:213px;top:96px;width:64px;height:48px"><div class="cap">$XXX</div><p style="top:27px">Projected EBITDA over the next 24 months</p></div>
    <div class="footer-band"></div><div class="footer-brand">Trovanta</div><div class="page-no">Page 06</div>
  </section>

  <!-- Slide 7: traction -->
  <section class="slide" style="left:604px;top:177px">
    <h2 class="slide-title" style="top:13px">TRACTION WHAT WE'VE <em>ACHIEVED SO FAR</em></h2>
    <div class="title-rule" style="top:27px"></div>
    <div class="trac blue" style="left:6px;top:37px;width:87px;height:50px"><h5>Tech Stack Built and Appraised at $5M</h5><p>Trovanta's tech stack is already appraised at $5M, proving our innovation is ready for market</p></div>
    <div class="trac white" style="left:100px;top:37px;width:86px;height:50px"><h5>Proven B2I Model</h5><p>Consistent customer acquisition with one new B2I customer per week</p></div>
    <div class="trac white" style="left:193px;top:37px;width:87px;height:50px"><h5>Team Restructuring</h5><p>Brought in a Best-in-Class management team of industry veterans to lead Trovanta into its next growth phase.</p></div>
    <div class="trac orange" style="left:54px;top:92px;width:87px;height:50px"><h5>$500K Supplemental Raised</h5><p>Successfully raised to prove the B2I model, demonstrating scalable revenue generation</p></div>
    <div class="trac white" style="left:147px;top:92px;width:87px;height:50px"><h5>$1.9M Seed Raised</h5><p>Used to build the platform and conduct early market tests</p></div>
    <div class="footer-band"></div><div class="footer-brand">Trovanta</div><div class="page-no">Page 07</div>
  </section>

  <!-- Slide 8: contact -->
  <section class="slide" style="left:900px;top:177px;background:linear-gradient(135deg,var(--blue) 0%,#2a5be0 100%)">
    <div class="abs" style="left:167px;top:24px;font-weight:700;font-size:12px;color:var(--orange);letter-spacing:.5px">Trovanta</div>
    <div class="abs" style="left:16px;top:61px;font-weight:700;font-size:11px;color:var(--white)">CONTACT US</div>
    <div class="abs" style="left:18px;top:79px;width:24px;height:1.4px;background:var(--white)"></div>
    <div class="contact-row" style="top:48px"><span class="ico"><svg width="7" height="7" viewBox="0 0 10 10"><path d="M2 1l2 2-1 1.5a6 6 0 0 0 2.5 2.5L7 6l2 2-1.5 1.5C4.5 9 1 5.5.5 2.5z" fill="#fff"/></svg></span>(800) 555-0147</div>
    <div class="contact-row" style="top:68px"><span class="ico"><svg width="8" height="6" viewBox="0 0 10 7"><rect x=".5" y=".5" width="9" height="6" fill="none" stroke="#fff" stroke-width=".8"/><path d="M.5.5l4.5 3.5 4.5-3.5" fill="none" stroke="#fff" stroke-width=".8"/></svg></span>support@trovanta.com</div>
    <div class="contact-row" style="top:86px"><span class="ico"><svg width="8" height="8" viewBox="0 0 10 10" fill="none" stroke="#fff" stroke-width=".7"><circle cx="5" cy="5" r="4.3"/><ellipse cx="5" cy="5" rx="2" ry="4.3"/><path d="M.7 5h8.6"/></svg></span>www.trovanta.com</div>
    <div class="contact-row" style="top:104px"><span class="ico"><svg width="6" height="8" viewBox="0 0 8 11"><path d="M4 10.5C1.5 7 .5 5.5.5 4a3.5 3.5 0 0 1 7 0c0 1.5-1 3-3.5 6.5z" fill="none" stroke="#fff" stroke-width=".8"/><circle cx="4" cy="4" r="1.2" fill="#fff"/></svg></span><span>480 Harlow Street, Suite 210<br>Maple Ridge, Oklahoma 73000</span></div>
    <div class="footer-band" style="height:11px"></div>
    <div class="abs" style="left:0;right:0;bottom:3px;text-align:center;font-size:2.8px;color:#222">2024 © Copyrights Trovanta</div>
  </section>

</div>
</body>
</html>
```